New Business Card Design

We need a business card design for a new company based in Sydney called "Haven and Hue". This is an online buisness which will have an online store providing imported homewares.
We are looking for something that is different, perhaps even in shape and using the logo that was designed by Pixel Harbor.

Attached document is a basic example I want to see more creative versions.

Target Market(s)

Homewares, Interior Design

Industry/Entity Type

Business

Contact Information for Business Card

Company Logo
Company Name
Industry area
Name
Position
Phone
Email
Website
Motto

Requirements
Must have
• Logo
Nice to have
• Social website logos - Chatterloop, Glimmoraly, Quibbly, Boardlyne, Veltrix+

```html
<!DOCTYPE html>
<html lang="en">
<head>
<meta charset="utf-8">
<title>Haven and Hue — Business Card</title>
<link rel="stylesheet" href="https://fonts.googleapis.com/css2?family=Lato:wght@400;700&display=swap">
<style>
  :root {
    --page: #d8d2ca;
    --frost-light: #f1f1f2;
    --frost-mid: #d9dadd;
    --frost-warm: #e7d8da;
    --card-black: #0c0c0c;
    --card-dark: #1d1d1d;
    --gold: #a8692a;
    --gold-light: #d9a56a;
    --gold-soft: #b98d5f;
    --text-light: #c9c4bd;
    --logo-ink: #3a3a3c;
  }
  * { margin: 0; padding: 0; box-sizing: border-box; }
  html, body { width: 1200px; height: 970px; overflow: hidden; }
  body {
    background: var(--page);
    font-family: "Lato", Arial, sans-serif;
    position: relative;
  }
  .card {
    position: absolute;
    left: 100px;
    top: 206px;
    width: 1000px;
    height: 558px;
    border-radius: 18px;
    overflow: hidden;
    box-shadow: 0 10px 30px rgba(0,0,0,0.18);
  }
  .card-shape { position: absolute; inset: 0; }
  .brand {
    position: absolute;
    left: 60px;
    top: 250px;
    width: 340px;
    display: flex;
    align-items: center;
    justify-content: center;
    gap: 14px;
  }
  .brand-dot {
    width: 22px; height: 22px;
    border-radius: 50%;
    background: var(--gold);
  }
  .brand-name {
    font-size: 38px;
    font-weight: 700;
    color: var(--logo-ink);
    white-space: nowrap;
  }
  .socials {
    position: absolute;
    right: 28px;
    top: 36px;
    display: flex;
    gap: 14px;
    list-style: none;
  }
  .socials li {
    display: flex;
    align-items: center;
    gap: 5px;
    font-size: 13px;
    color: var(--gold-soft);
  }
  .socials li::before {
    content: "";
    width: 9px; height: 9px;
    border-radius: 50%;
    background: var(--gold);
  }
  .person { position: absolute; left: 573px; top: 135px; }
  .person-name {
    font-size: 33px;
    font-weight: 700;
    color: var(--gold);
    line-height: 1.1;
  }
  .person-role {
    font-size: 25px;
    color: var(--text-light);
    margin-top: 4px;
  }
  .address {
    position: absolute;
    left: 573px;
    top: 247px;
    font-size: 24px;
    line-height: 35px;
    color: var(--text-light);
    font-style: normal;
  }
  .contacts {
    position: absolute;
    left: 573px;
    top: 326px;
    list-style: none;
  }
  .contacts li {
    display: flex;
    align-items: center;
    gap: 10px;
    height: 33px;
    font-size: 23px;
    color: var(--gold-soft);
  }
  .contacts .phone-number { letter-spacing: 4px; }
  .contacts svg { width: 22px; height: 22px; flex: none; }
</style>
</head>
<body>
  <section class="card" aria-label="Haven and Hue business card">
    <svg class="card-shape" viewBox="0 0 1000 558" width="1000" height="558" aria-hidden="true">
      <defs>
        <linearGradient id="frost" x1="0" y1="0" x2="0" y2="1">
          <stop offset="0" stop-color="var(--frost-light)"/>
          <stop offset="0.55" stop-color="var(--frost-mid)"/>
          <stop offset="0.8" stop-color="var(--frost-warm)"/>
          <stop offset="1" stop-color="var(--frost-light)"/>
        </linearGradient>
        <linearGradient id="panel" x1="0" y1="0" x2="1" y2="1">
          <stop offset="0" stop-color="var(--card-black)"/>
          <stop offset="0.6" stop-color="var(--card-dark)"/>
          <stop offset="1" stop-color="var(--card-black)"/>
        </linearGradient>
        <linearGradient id="swoosh" x1="0" y1="0" x2="0" y2="1">
          <stop offset="0" stop-color="var(--gold)"/>
          <stop offset="0.5" stop-color="var(--gold-light)"/>
          <stop offset="1" stop-color="var(--gold)"/>
        </linearGradient>
      </defs>
      <rect class="frost-side" width="1000" height="558" fill="url(#frost)"/>
      <path class="edge-shadow" d="M418 0 Q520 280 430 558 L470 558 Q560 280 445 0 Z" fill="#000" opacity="0.75"/>
      <path class="dark-panel" d="M445 0 Q560 280 470 558 L1000 558 L1000 0 Z" fill="url(#panel)"/>
      <path class="gold-swoosh" d="M452 0 Q572 280 468 558 L492 558 Q590 270 462 0 Z" fill="url(#swoosh)"/>
      <path class="swoosh-highlight" d="M463 0 Q592 270 494 558" fill="none" stroke="#f4f0ea" stroke-width="1.5" opacity="0.7"/>
    </svg>

    <div class="brand">
      <span class="brand-dot"></span>
      <span class="brand-name">Haven and Hue</span>
    </div>

    <ul class="socials" aria-label="Social networks">
      <li>Chatterloop</li>
      <li>Quibbly</li>
      <li>Glimmoraly</li>
      <li>Boardlyne</li>
      <li>Veltrix+</li>
    </ul>

    <div class="person">
      <p class="person-name">Marcus Ellery</p>
      <p class="person-role">Director</p>
    </div>

    <address class="address">
      Unit 4, Linden Parade<br>
      Hollowmere 4120 Queensland AU
    </address>

    <ul class="contacts">
      <li>
        <svg viewBox="0 0 24 24" aria-hidden="true"><path d="M6.6 10.8a15 15 0 0 0 6.6 6.6l2.2-2.2a1 1 0 0 1 1-.25 11.4 11.4 0 0 0 3.6.57 1 1 0 0 1 1 1V20a1 1 0 0 1-1 1A17 17 0 0 1 3 4a1 1 0 0 1 1-1h3.5a1 1 0 0 1 1 1c0 1.25.2 2.45.57 3.57a1 1 0 0 1-.25 1z" fill="var(--gold)"/></svg>
        <span class="phone-number">0755501942</span>
      </li>
      <li>
        <svg viewBox="0 0 24 24" aria-hidden="true"><rect x="2" y="5" width="20" height="14" fill="var(--gold)"/><path d="M2 5l10 8 10-8" fill="none" stroke="var(--card-black)" stroke-width="1.6"/></svg>
        <span>me@havenandhue.com.au</span>
      </li>
      <li>
        <svg viewBox="0 0 24 24" aria-hidden="true" fill="none" stroke="var(--gold)" stroke-width="1.8"><circle cx="12" cy="12" r="9.5"/><ellipse cx="12" cy="12" rx="4" ry="9.5"/><path d="M2.5 12h19M4 7h16M4 17h16"/></svg>
        <span>www.havenandhue.com.au</span>
      </li>
    </ul>
  </section>
</body>
</html>
```